Business Card Update, need to bring life to the card, two sided color

We need a new business card design, are moving and changing addresses and need a new look, we have the logos already attached but need a new style moving forward. Can incorporate the color of the logo (The Green) as well, maybe a solid back? We deal with safety products revolving around static electricity and safety lighting. Would like to keep same font in second logo as well.

Target Market(s)

Electrical Safety, Lighting

Contact Information for Business Card

Dale Fenwick
Vice President
Office: 770-555-4821
Cell: 770-555-3067
dale@tkfenwick.example
www.tkfenwick.example
4700 West Harbor Boulevard
Suite #150
Roswell, GA 30076

Font styles to use
Serif
Sans Serif

Requirements
Must have
• Since 1918
Nice to have
• Could use the 100 Year Logo for back of card, would like the back of card to be the same green as logo.
Should not have
• No black cards please.

```html
<!DOCTYPE html>
<html lang="en">
<head>
<meta charset="utf-8">
<title>T.K. Fenwick Business Card</title>
<link rel="stylesheet" href="https://fonts.googleapis.com/css2?family=Roboto:wght@400;500;700&display=swap">
<style>
  :root {
    --brand-green: #009a5c;
    --paper: #ffffff;
    --ink-grey: #3a3a3a;
    --stage: #e6e8e7;
    --on-green: #ffffff;
  }
  * { box-sizing: border-box; margin: 0; padding: 0; }
  html, body {
    width: 1200px; height: 768px; overflow: hidden;
    background: var(--stage);
    font-family: "Roboto", Arial, sans-serif;
  }
  .canvas {
    position: relative; width: 1200px; height: 768px;
    display: flex; align-items: center; justify-content: center; gap: 50px;
  }
  .card {
    position: relative; width: 530px; height: 303px;
    border-radius: 20px; overflow: hidden;
    box-shadow: 0 10px 28px rgba(0,0,0,.18);
  }
  /* Front: white side */
  .card-front { background: var(--paper); }
  .company {
    position: absolute; left: 62px; top: 96px;
    display: flex; align-items: center; gap: 16px;
    color: var(--brand-green); font-weight: 700;
  }
  .company-dot {
    width: 72px; height: 72px; border-radius: 50%;
    background: var(--brand-green); flex: none;
  }
  .company-name { font-size: 34px; line-height: 1; }
  .company-sub { font-size: 16px; line-height: 1.15; margin-top: 4px; }
  .company-since { font-size: 13px; font-weight: 500; letter-spacing: 2px; margin-top: 4px; text-transform: uppercase; }
  .front-url {
    position: absolute; left: 0; right: 0; bottom: 54px;
    text-align: center; font-size: 14px; letter-spacing: 5px;
    color: var(--ink-grey);
  }
  /* Back: green side */
  .card-back { background: var(--brand-green); color: var(--on-green); }
  .product-art {
    position: absolute; left: 70px; top: 40px; width: 110px; height: 220px;
    border-radius: 55px 55px 14px 14px;
    background: linear-gradient(180deg, rgba(255,255,255,.35), rgba(255,255,255,.18));
  }
  .contact {
    position: absolute; left: 250px; top: 30px; right: 16px;
  }
  .person-name { font-size: 24px; font-weight: 700; line-height: 1; }
  .person-title { font-size: 15px; font-weight: 500; margin-top: 3px; }
  .address { font-size: 14px; line-height: 1.3; margin-top: 14px; }
  .lines { list-style: none; margin-top: 10px; }
  .lines li {
    display: flex; align-items: center; gap: 10px;
    font-size: 14px; line-height: 20px;
  }
  .lines svg { width: 14px; height: 14px; flex: none; fill: var(--on-green); }
</style>
</head>
<body>
<main class="canvas">
  <section class="card card-front" aria-label="Card front">
    <div class="company">
      <span class="company-dot"></span>
      <div>
        <div class="company-name">T.K. Fenwick</div>
        <div class="company-sub">Manufacturing Company, Inc.</div>
        <div class="company-since">Since 1918</div>
      </div>
    </div>
    <p class="front-url">www.tkfenwick.example</p>
  </section>

  <section class="card card-back" aria-label="Card back">
    <div class="product-art" role="img" aria-label="Large white product illustration of a safety light tube"></div>
    <div class="contact">
      <h1 class="person-name">Dale Fenwick</h1>
      <p class="person-title">Vice President</p>
      <p class="address">4700 West Harbor Boulevard<br>Suite #150<br>Roswell, GA 30076</p>
      <ul class="lines">
        <li><svg viewBox="0 0 16 16"><path d="M3.5 1l3 3-1.6 1.8c.8 1.8 2.4 3.4 4.3 4.3L11 8.5l3 3-2 2.5C6.3 13.5 2.5 9.7 1 4z"/></svg>770 555 4821</li>
        <li><svg viewBox="0 0 16 16"><path d="M4 0h8v16H4zM5.5 2v10h5V2zM7 13.2h2v1.4H7z"/></svg>770 555 3067</li>
        <li><svg viewBox="0 0 16 16"><path d="M4 1h7v4H4zM1 6h14v7h-3v2H4v-2H1zM5 10v3h6v-3z"/></svg>770 555 7190</li>
        <li><svg viewBox="0 0 16 16"><path d="M1 3h14v10H1zM2.5 4.5v.4L8 9l5.5-4.1v-.4zM2.5 6.7v4.8h11V6.7L8 10.8z"/></svg>dale@tkfenwick.example</li>
        <li><svg viewBox="0 0 16 16"><path d="M8 1a7 7 0 1 0 0 14A7 7 0 0 0 8 1zm0 1.5c.9 0 1.8 2 2 4.5H6c.2-2.5 1.1-4.5 2-4.5zM6 9h4c-.2 2.5-1.1 4.5-2 4.5S6.2 11.5 6 9z"/></svg>www.tkfenwick.example</li>
      </ul>
    </div>
  </section>
</main>
</body>
</html>
```